Brightfield Ventures Inc. Letterhead

Creation of attractive and eye catching letterhead for a business start-up for the construction industry. Letterhead must relate to construction, but avoid standard hammer and tools in the design.

I forgot to add some details, sorry about that. Some pertinent info: Ph: 916-555-0187 brightfieldventures.example 448 Willowmere Ave, Ste 210 Folsom, CA 95999 info@brightfieldventures.example not sure if slogan should be in there" “Connecting construction professionals to create a purpose driven industry.” must be able to be used in word. Thanks!

```html
<!DOCTYPE html>
<html lang="en">
<head>
<meta charset="utf-8">
<title>Brightfield Ventures Inc. Letterhead</title>
<link href="https://fonts.googleapis.com/css2?family=Montserrat:wght@500;600;700&family=Noto+Sans:wght@400&display=swap" rel="stylesheet">
<style>
  :root {
    --navy: #1b2a78;
    --red: #c0161a;
    --ink: #1d1d1f;
    --paper: #ffffff;
    --backdrop: #eceff0;
    --header-tint: #eef2f2;
  }
  * { margin: 0; padding: 0; box-sizing: border-box; }
  html, body { width: 1200px; height: 1200px; overflow: hidden; background: var(--backdrop); }
  .letterhead {
    position: absolute; left: 160px; top: 30px;
    width: 880px; height: 1140px;
    background: var(--paper);
    box-shadow: 0 4px 18px rgba(0,0,0,0.12);
    overflow: hidden;
  }
  .header-texture {
    position: absolute; left: 0; top: 0; width: 100%; height: 160px;
    background: linear-gradient(100deg, var(--header-tint) 0%, #f7f9f9 55%, var(--header-tint) 100%);
  }
  .contact-bar {
    position: absolute; left: 70px; top: 36px; width: 16px; height: 124px;
    background: var(--red);
  }
  .contact-icons { position: absolute; left: 70px; top: 40px; }
  .contact-list {
    position: absolute; left: 96px; top: 38px;
    font-family: "Montserrat", sans-serif; font-weight: 600;
    font-size: 13px; line-height: 22px; color: var(--navy);
    list-style: none;
  }
  .contact-list .address { line-height: 15px; margin-top: 4px; }
  .header-rule {
    position: absolute; left: 70px; top: 160px; width: 740px; height: 2px;
    background: var(--red);
  }
  .brand {
    position: absolute; right: 70px; top: 104px;
    font-family: "Montserrat", sans-serif; font-weight: 700;
    font-size: 18px; letter-spacing: 0.5px; color: var(--navy);
    display: flex; align-items: center; gap: 8px;
  }
  .brand-mark { width: 12px; height: 12px; background: var(--red); }
  .letter-body {
    position: absolute; left: 110px; top: 230px; width: 660px;
    font-family: "Noto Sans", sans-serif; font-size: 14.5px;
    line-height: 19px; color: var(--ink); text-align: justify;
  }
  .letter-body p { margin-bottom: 14px; }
  .letter-body .salutation { margin-bottom: 24px; }
  .letter-body .closing { margin-top: 26px; }
  .brand-watermark {
    position: absolute; left: 40px; top: 930px;
    font-family: "Montserrat", sans-serif; font-weight: 700;
    font-size: 54px; color: var(--navy); opacity: 0.08;
  }
  .footer-band { position: absolute; left: 0; bottom: 0; width: 100%; height: 36px; }
</style>
</head>
<body>
<main class="letterhead">
  <div class="header-texture" role="img" aria-label="Soft pale geometric texture behind the header"></div>

  <div class="contact-bar"></div>
  <svg class="contact-icons" width="16" height="110" viewBox="0 0 16 110" aria-hidden="true">
    <g fill="none" stroke="#fff" stroke-width="1.4">
      <circle cx="8" cy="9" r="5.5"/>
      <path d="M5.8 6.5 q0 4 4 4.8" stroke-linecap="round"/>
      <circle cx="8" cy="31" r="5.5"/>
      <path d="M5 29.5 h6 v4 h-6 z M5 29.5 l3 2.2 l3 -2.2"/>
      <circle cx="8" cy="53" r="5.5"/>
      <path d="M2.5 53 h11 M8 47.5 q-3 5.5 0 11 M8 47.5 q3 5.5 0 11"/>
      <circle cx="8" cy="77" r="5.5"/>
      <path d="M8 80 l-2.2 -3 a2.4 2.4 0 1 1 4.4 0 z"/>
    </g>
  </svg>
  <ul class="contact-list">
    <li>916-555-0187</li>
    <li>info@brightfieldventures.example</li>
    <li>brightfieldventures.example</li>
    <li class="address">448 Willowmere Ave,<br>Ste 210 Folsom, CA 95999</li>
  </ul>

  <div class="brand"><span class="brand-mark"></span>Brightfield Ventures</div>
  <div class="header-rule"></div>

  <section class="letter-body">
    <p class="salutation">Dear :</p>
    <p>Lorem ipsum dolor sit amet, consectetur adipiscing elit. Aenean ut ipsum eget massa hendrerit vestibulum vel in velit. Donec pretium neque velit.</p>
    <p>Aliquam porta lectus nec mauris ornare venenatis. Vivamus non est turpis, et cursus sem. Mauris vehicula erat in diam auctor at bibendum nisl lacinia.</p>
    <p>Morbi imperdiet neque vehicula nunc convallis gravida. Vestibulum iaculis pretium placerat. Integer consequat, est sit amet facilisis eleifend, nibh nibh varius orci, eget dapibus arcu dui non purus. Pellentesque in magna mauris. Duis enim sapien, dictum vitae condimentum a, pulvinar vel lacus. Mauris et molestie nibh. Vestibulum vitae nulla at metus elementum porta sit amet interdum elit. Nulla sollicitudin neque eu nulla volutpat congue.</p>
    <p>Etiam pellentesque, velit id dapibus fermentum, turpis sapien ornare dui, ac tincidunt ligula odio congue purus. Nunc sed ante dui, in porta lectus. Cras nec sem lorem. In hac habitasse platea dictumst. Maecenas id diam quis dui porta tristique. Sed id egestas felis. Donec ullamcorper mattis posuere. Phasellus fermentum eleifend tortor vel dapibus. Vestibulum ante ipsum.</p>
    <p>Etiam pellentesque, velit id dapibus fermentum, turpis sapien ornare dui, ac tincidunt ligula odio congue purus. Nunc sed ante dui, in porta lectus. Cras nec sem lorem. In hac habitasse platea dictumst. Maecenas id diam quis dui porta tristique. Sed id egestas felis. Donec ullamcorper mattis posuere. Phasellus fermentum eleifend tortor vel dapibus. Vestibulum ante ipsum.</p>
    <p class="closing">Sincerely,</p>
  </section>

  <div class="brand-watermark" aria-hidden="true">Brightfield Ventures</div>

  <svg class="footer-band" viewBox="0 0 880 36" preserveAspectRatio="none" aria-hidden="true">
    <rect x="0" y="0" width="880" height="36" fill="var(--navy)"/>
    <polygon points="800,0 880,0 880,36 830,36" fill="var(--red)"/>
    <polygon points="760,0 772,0 802,36 790,36" fill="#fff"/>
    <polygon points="778,0 790,0 820,36 808,36" fill="var(--red)"/>
    <polygon points="792,0 800,0 830,36 822,36" fill="#fff"/>
  </svg>
</main>
</body>
</html>
```